New Business Card Design Project

We would like a business card that represents the sale of boat, home, auto, and life insurance.

The logo can change colors to meet the look of the design if needed.

Industry/Entity Type

Business

```html
<!DOCTYPE html>
<html lang="en">
<head>
<meta charset="UTF-8">
<title>Corva Financial – Business Card</title>
<link href="https://fonts.googleapis.com/css2?family=Josefin+Sans:wght@400&family=Open+Sans:wght@400;600&display=swap" rel="stylesheet">
<style>
  :root {
    --page-bg: #e4e6e8;
    --teal: #3b7487;
    --ink: #2b2f33;
    --muted: #555b61;
    --card-white: #ffffff;
    --grid-tone: #eef0f2;
    --shadow: rgba(0, 0, 0, 0.18);
  }
  * { margin: 0; padding: 0; box-sizing: border-box; }
  html, body { width: 1200px; height: 676px; overflow: hidden; }
  body {
    background: var(--page-bg);
    font-family: "Josefin Sans", sans-serif;
    position: relative;
  }
  .card {
    position: absolute;
    top: 195px;
    width: 500px;
    height: 286px;
    box-shadow: 0 6px 18px var(--shadow);
    overflow: hidden;
  }

  .wordmark {
    position: absolute;
    display: flex;
    align-items: center;
    white-space: nowrap;
    font-family: "Josefin Sans", sans-serif;
    font-weight: 400;
    line-height: 1;
  }
  .wordmark-dot { flex: none; border-radius: 50%; }

  /* Front */
  .card-front { left: 70px; background: var(--teal); }
  .card-front .wordmark {
    left: 150px;
    top: 124px;
    gap: 14px;
    font-size: 36px;
    color: #fff;
  }
  .card-front .wordmark-dot { width: 26px; height: 26px; background: #fff; }

  /* Back */
  .card-back { left: 630px; background: var(--card-white); }
  .back-texture {
    position: absolute;
    inset: 0 0 44px 0;
    background: linear-gradient(135deg, var(--card-white) 0%, var(--grid-tone) 100%);
  }
  .card-back .wordmark {
    left: 34px;
    top: 56px;
    gap: 9px;
    font-size: 22px;
    color: var(--ink);
  }
  .card-back .wordmark-dot { width: 16px; height: 16px; background: var(--teal); }

  .contact-list {
    position: absolute;
    left: 34px;
    top: 112px;
    list-style: none;
    font-family: "Open Sans", sans-serif;
    font-size: 12px;
    line-height: 17px;
    color: var(--ink);
  }
  .contact-list li { display: flex; align-items: center; gap: 8px; }
  .contact-list svg { width: 10px; height: 10px; flex: none; }
  .person {
    position: absolute;
    right: 30px;
    top: 150px;
    text-align: right;
    font-family: "Open Sans", sans-serif;
  }
  .person-name {
    font-weight: 600;
    font-size: 17px;
    letter-spacing: 1px;
    color: var(--teal);
  }
  .person-title {
    font-size: 13px;
    letter-spacing: 0.5px;
    color: var(--muted);
  }
  .back-band {
    position: absolute;
    left: 0; right: 0; bottom: 0;
    height: 44px;
    background: var(--teal);
    border-top: 6px solid var(--ink);
  }
</style>
</head>
<body>

  <section class="card card-front" aria-label="Card front">
    <div class="wordmark">
      <span class="wordmark-dot"></span>
      <span class="wordmark-name">Corva Financial</span>
    </div>
  </section>

  <section class="card card-back" aria-label="Card back">
    <div class="back-texture"></div>

    <div class="wordmark">
      <span class="wordmark-dot"></span>
      <span class="wordmark-name">Corva Financial</span>
    </div>

    <ul class="contact-list">
      <li>
        <svg viewBox="0 0 10 10"><path d="M2 1h2l1 2-1 1c.6 1.2 1.4 2 2.6 2.6l1-1 2 1v2c0 .6-.4 1-1 1C4.4 9.6.4 5.6 1 2c0-.6.4-1 1-1z" fill="var(--teal)"/></svg>
        0123 456 789
      </li>
      <li>
        <svg viewBox="0 0 10 10"><rect x="1" y="3" width="8" height="5" rx="1" fill="var(--teal)"/><rect x="3" y="1" width="4" height="2" fill="var(--teal)"/></svg>
        0123 456 789
      </li>
      <li>
        <svg viewBox="0 0 10 10"><rect x="2.5" y="0.5" width="5" height="9" rx="1" fill="none" stroke="var(--teal)"/></svg>
        0123 456 789
      </li>
      <li>
        <svg viewBox="0 0 10 10"><rect x="0.5" y="2" width="9" height="6" fill="var(--teal)"/><path d="M0.5 2l4.5 3.5L9.5 2" fill="none" stroke="#fff"/></svg>
        yourmail@mail.com
      </li>
      <li>
        <svg viewBox="0 0 10 10"><circle cx="5" cy="5" r="4.2" fill="none" stroke="var(--teal)"/><path d="M0.8 5h8.4M5 0.8c-2.2 2.4-2.2 6 0 8.4M5 0.8c2.2 2.4 2.2 6 0 8.4" fill="none" stroke="var(--teal)" stroke-width="0.7"/></svg>
        www.yourwebsite.com
      </li>
    </ul>

    <div class="person">
      <div class="person-name">Your name</div>
      <div class="person-title">Your title</div>
    </div>

    <div class="back-band"></div>
  </section>

</body>
</html>
```